Need a website setup for our new removalist business.
Our business is called Harbour Lane Removals and would like a website setup.
We don’t have a website, logo or design as of yet. Our truck is blue so something possibly that works and can incorporate the blue.

```html
<!DOCTYPE html>
<html lang="en">
<head>
<meta charset="utf-8">
<title>Harbour Lane Removals</title>
<link rel="stylesheet" href="https://fonts.googleapis.com/css2?family=Lexend:wght@400;500;600&family=Questrial&display=swap">
<style>
:root{
  --blue:#1f7fd1;
  --blue-deep:#1565b3;
  --navy:#0f2440;
  --ink:#1d1d1f;
  --text:#2b2b2b;
  --muted:#555;
  --dark:#252525;
  --white:#fff;
  --line:#e4e8ee;
}
*{margin:0;padding:0;box-sizing:border-box}
html,body{width:1200px;height:3065px;overflow:hidden;background:var(--white)}
body{font-family:"Questrial",sans-serif;color:var(--text);position:relative}
.abs{position:absolute}
.head{font-family:"Lexend",sans-serif;text-transform:uppercase}
.btn{position:absolute;display:flex;align-items:center;justify-content:center;background:var(--blue);color:var(--white);font-family:"Lexend",sans-serif;font-size:14px;text-transform:uppercase;border-radius:4px}
/* top bar */
.topline{left:0;top:0;width:430px;height:4px;background:var(--blue)}
.topbar{left:428px;top:0;width:580px;height:38px;background:var(--blue);clip-path:polygon(0 0,100% 0,100% 100%,34px 100%)}
.topbar span{position:absolute;top:11px;color:var(--white);font-size:12px;font-family:"Lexend",sans-serif}
.topcontact{left:1005px;top:0;width:195px;height:38px;background:var(--dark);color:var(--white);font-family:"Lexend",sans-serif;font-size:14px;display:flex;align-items:center;justify-content:center}
.brand{left:110px;top:28px;width:150px;font-family:"Lexend",sans-serif;font-weight:600;font-size:15px;line-height:17px;color:var(--navy);text-transform:uppercase;display:flex;align-items:center;gap:8px}
.brand i{width:22px;height:22px;background:var(--blue);flex:none}
.nav{top:69px;font-family:"Lexend",sans-serif;font-size:14px;color:var(--ink)}
.nav.on{color:var(--blue)}
.search{left:1053px;top:59px;width:34px;height:34px;border-radius:50%;background:var(--blue)}
/* hero */
.hero{left:0;top:110px;width:1200px;height:441px;background:linear-gradient(100deg,#0c1a2c 0%,#14304f 45%,#1b4d86 70%,#0e2542 100%)}
.hero h1{position:absolute;left:108px;top:58px;font-family:"Lexend",sans-serif;font-weight:600;font-size:36px;color:var(--blue);letter-spacing:.5px}
.hero h2{position:absolute;left:108px;top:110px;font-family:"Lexend",sans-serif;font-weight:600;font-size:24px;color:var(--white)}
.hero p{position:absolute;left:108px;top:158px;width:500px;font-size:16.5px;line-height:35px;color:var(--white)}
/* features */
.feat{top:492px;width:318px;height:279px;background:var(--blue);border-radius:6px 6px 0 0;overflow:hidden}
.feat h3{height:60px;display:flex;align-items:center;justify-content:center;font-family:"Lexend",sans-serif;font-weight:400;font-size:18px;color:var(--white);text-transform:uppercase}
.feat div{height:219px}
/* about */
.aframe{left:120px;top:855px;width:305px;height:200px;border:1.5px solid var(--blue)}
.aphoto1{left:112px;top:865px;width:305px;height:391px;background:linear-gradient(160deg,#c9b79f,#8d7156 60%,#4a5d7b)}
.aphoto2{left:318px;top:1022px;width:250px;height:306px;background:var(--white);padding:5px}
.aphoto2 div{width:100%;height:100%;background:linear-gradient(180deg,#a9b3b5 0%,#7d8a83 45%,#5b5f60 100%)}
.h2{font-family:"Lexend",sans-serif;font-weight:600;font-size:33px;text-transform:uppercase;color:var(--ink);display:flex;align-items:center;gap:14px}
.h2 b{color:var(--blue);font-weight:600}
.h2 i{display:block;width:56px;height:3px;background:var(--blue)}
.about p{font-size:15px;line-height:34px;color:var(--text);margin-bottom:7px}
/* services */
.services{left:0;top:1403px;width:1200px;height:476px;background:linear-gradient(90deg,#2a7ec9,#1f7fd1 40%,#2b86d6)}
.svc{top:143px;width:150px;height:150px;border:1.5px solid var(--white);clip-path:polygon(30px 0,100% 0,100% 100%,0 100%,0 30px);display:flex;align-items:center;justify-content:center}
.svc.on{background:#000;border-color:#000}
.svcborder{position:absolute;left:-1px;top:-1px}
.svclabel{top:320px;font-family:"Lexend",sans-serif;font-size:17px;color:var(--white);text-transform:uppercase;text-align:center;width:240px}
/* testimonials */
.tcard{top:2119px;width:312px;height:364px;background:var(--white);border:1px solid var(--line);box-shadow:0 2px 8px rgba(0,0,0,.08);border-radius:4px}
.tcard p{position:absolute;left:18px;right:18px;top:36px;text-align:center;font-size:15px;line-height:33.5px;color:var(--text)}
.avatar{position:absolute;left:50px;top:252px;width:78px;height:84px;background:linear-gradient(180deg,#c8d3de,#8aa0b6);clip-path:polygon(50% 0,100% 25%,100% 75%,50% 100%,0 75%,0 25%)}
.tname{position:absolute;left:151px;top:264px;font-family:"Lexend",sans-serif;font-size:16px;color:var(--blue);text-transform:uppercase}
.trole{position:absolute;left:151px;top:298px;font-family:"Lexend",sans-serif;font-size:12.5px;color:var(--ink);text-transform:uppercase}
/* quote */
.quote{left:0;top:2635px;width:1200px;height:117px;background:var(--blue)}
.quote .tab{position:absolute;left:0;top:0;width:292px;height:117px;background:var(--blue-deep);clip-path:polygon(0 0,262px 0,292px 58px,262px 117px,0 117px)}
.quote h3{position:absolute;left:33px;top:41px;font-family:"Lexend",sans-serif;font-weight:600;font-size:24px;color:var(--white)}
.field{position:absolute;top:39px;width:164px;height:39px;background:#3a90dc;color:var(--white);font-family:"Lexend",sans-serif;font-size:12.5px;padding:12px 13px}
.submit{position:absolute;left:1006px;top:39px;width:164px;height:39px;background:var(--white);color:var(--blue);font-family:"Lexend",sans-serif;font-size:15px;display:flex;align-items:center;justify-content:center}
/* footer */
.footer{left:0;top:2752px;width:1200px;height:313px;background:var(--dark)}
.fbrand{position:absolute;left:84px;top:84px;width:210px;font-family:"Lexend",sans-serif;font-weight:600;font-size:23px;line-height:26px;color:var(--white);text-transform:uppercase;display:flex;align-items:center;gap:12px}
.fbrand i{width:30px;height:30px;background:var(--blue);flex:none}
.fh{position:absolute;top:62px;font-family:"Lexend",sans-serif;font-size:17px;color:var(--blue)}
.fl{position:absolute;font-family:"Lexend",sans-serif;font-size:13px;color:var(--white);line-height:34.5px}
.ficon{position:absolute;width:34px;height:34px;border-radius:50%;background:#333;display:flex;align-items:center;justify-content:center}
.fc{position:absolute;font-family:"Lexend",sans-serif;font-size:12px;color:var(--white)}
.frule{position:absolute;left:56px;top:265px;width:1090px;height:1px;background:#444}
.copy{position:absolute;left:0;width:1200px;top:281px;text-align:center;font-family:"Lexend",sans-serif;font-size:12px;color:var(--white)}
.copy b{color:var(--blue);font-weight:400}
</style>
</head>
<body>

<!-- top bar -->
<div class="abs topline"></div>
<div class="abs topbar">
  <svg class="abs" style="left:72px;top:12px" width="13" height="13" viewBox="0 0 24 24" fill="#fff"><path d="M6.6 10.8a15.1 15.1 0 0 0 6.6 6.6l2.2-2.2c.3-.3.7-.4 1-.2 1.1.4 2.3.6 3.6.6.6 0 1 .4 1 1V20c0 .6-.4 1-1 1A17 17 0 0 1 3 4c0-.6.4-1 1-1h3.5c.6 0 1 .4 1 1 0 1.3.2 2.5.6 3.6.1.3 0 .7-.2 1z"/></svg>
  <span style="left:98px">+1 555 010 2040</span>
  <div class="abs" style="left:240px;top:0;width:1px;height:38px;background:rgba(255,255,255,.3)"></div>
  <svg class="abs" style="left:273px;top:13px" width="14" height="11" viewBox="0 0 24 18" fill="#fff"><path d="M0 0h24v18H0z" fill="none"/><path d="M1 1h22v16H1z" fill="#fff"/><path d="M1 1l11 9 11-9" stroke="#1f7fd1" stroke-width="2" fill="none"/></svg>
  <span style="left:305px">HELLO@HARBOURLANEREMOVALS.EXAMPLE</span>
</div>
<div class="abs topcontact">CONTACT US</div>

<!-- header -->
<div class="abs brand"><i></i><span>Harbour Lane Removals</span></div>
<div class="abs nav on" style="left:478px">HOME</div>
<div class="abs nav" style="left:556px">SERVICES</div>
<div class="abs nav" style="left:660px">ABOUT US</div>
<div class="abs nav" style="left:770px">TESTIMONIALS</div>
<div class="abs nav" style="left:909px">GET A QUOTE</div>
<div class="abs search">
  <svg width="34" height="34" viewBox="0 0 34 34"><circle cx="15.5" cy="15.5" r="5.5" stroke="#fff" stroke-width="2" fill="none"/><path d="M19.5 19.5l4.5 4.5" stroke="#fff" stroke-width="2"/></svg>
</div>

<!-- hero -->
<section class="abs hero" role="img" aria-label="Night highway with a glowing wireframe removal truck">
  <h1>SEAMLESS MOVES FROM</h1>
  <h2>EAST TO WEST, ACROSS AUSTRALIA</h2>
  <p>Lorem ipsum dolor sit amet, consectetur adipiscing elit, sed do eiusmod tempor incididunt ut labore et dolore magna aliqua enim ad minim veniam.</p>
</section>
<div class="btn" style="left:111px;top:401px;width:161px;height:37px">Get a free quote</div>

<!-- feature cards -->
<div class="abs feat" style="left:112px"><h3>Reliability</h3><div role="img" aria-label="Truck on a highway at sunset" style="background:linear-gradient(180deg,#c98a86 0%,#5e6f8c 45%,#2b3b54 100%)"></div></div>
<div class="abs feat" style="left:441px"><h3>Customer Service</h3><div role="img" aria-label="Customer service team wearing headsets" style="background:linear-gradient(180deg,#eef0f2 0%,#c9c1b6 60%,#8f7f6e 100%)"></div></div>
<div class="abs feat" style="left:770px"><h3>Efficiency</h3><div role="img" aria-label="Truck with a glowing world map on the trailer" style="background:linear-gradient(180deg,#6d8fb5 0%,#2d4c74 50%,#15243a 100%)"></div></div>

<!-- about -->
<div class="abs aframe"></div>
<div class="abs aphoto1" role="img" aria-label="Smiling mover carrying a cardboard box from a van"></div>
<div class="abs aphoto2"><div role="img" aria-label="Trucks travelling along a motorway"></div></div>
<div class="abs h2" style="left:634px;top:852px"><span><b>About</b> Us</span><i></i></div>
<div class="abs about" style="left:634px;top:907px;width:460px">
  <p>Lorem ipsum dolor sit amet, consectetur adipiscing elit, sed do eiusmod tempor incididunt ut labore et dolore magna aliqua. Ut enim ad minim veniam, quis nostrud exercitation ullamco laboris nisi ut aliquip ex ea commodo consequat. Duis aute irure dolor in reprehenderit in voluptate velit esse cillum dolore eu fugiat nulla pariatur.</p>
  <p>Lorem ipsum dolor sit amet, consectetur adipiscing elit, sed do eiusmod tempor incididunt ut labore et dolore magna aliqua enim ad minim veniam, quis nostrud exercitation ullamco laboris nisi ut aliquip ex ea commodo consequat.</p>
</div>
<div class="btn" style="left:634px;top:1285px;width:196px;height:38px">Read more about us</div>

<!-- services -->
<section class="abs services">
  <div class="abs h2" style="left:463px;top:52px;color:#fff"><span>Our Services</span><i style="background:#fff"></i></div>

  <div class="abs svc" style="left:178px">
    <svg class="svcborder" width="150" height="150"><path d="M30 .75H149.25V149.25H.75V30Z" fill="none" stroke="#fff" stroke-width="1.5"/></svg>
    <svg width="74" height="70" viewBox="0 0 74 70" fill="none" stroke="#fff" stroke-width="2"><rect x="2" y="30" width="38" height="38"/><rect x="40" y="40" width="30" height="28"/><rect x="44" y="8" width="20" height="32"/><rect x="10" y="14" width="18" height="16"/><path d="M15 36h8M48 50h6M58 56l0 8M55 59l3-3 3 3"/></svg>
  </div>
  <div class="abs svc on" style="left:417px">
    <svg width="74" height="76" viewBox="0 0 74 76" fill="none" stroke="#fff" stroke-width="2.2"><rect x="10" y="4" width="54" height="24" rx="2"/><rect x="6" y="28" width="62" height="38" rx="3"/><path d="M14 12h46M14 20h46M18 38h38M18 46h38M18 54h38"/><rect x="10" y="66" width="12" height="8"/><rect x="52" y="66" width="12" height="8"/><path d="M2 30v10M72 30v10"/></svg>
  </div>
  <div class="abs svc" style="left:672px">
    <svg class="svcborder" width="150" height="150"><path d="M30 .75H149.25V149.25H.75V30Z" fill="none" stroke="#fff" stroke-width="1.5"/></svg>
    <svg width="90" height="74" viewBox="0 0 90 74" fill="none" stroke="#fff" stroke-width="2"><rect x="24" y="6" width="22" height="16"/><path d="M35 22v6M28 28h14"/><rect x="4" y="26" width="14" height="30"/><path d="M20 36h40v24H20z"/><path d="M60 44h14l12 10v10H60"/><circle cx="14" cy="66" r="5"/><circle cx="40" cy="66" r="5"/><circle cx="76" cy="66" r="5"/><rect x="50" y="10" width="10" height="24"/></svg>
  </div>
  <div class="abs svc" style="left:931px">
    <svg class="svcborder" width="150" height="150"><path d="M30 .75H149.25V149.25H.75V30Z" fill="none" stroke="#fff" stroke-width="1.5"/></svg>
    <svg width="74" height="74" viewBox="0 0 74 74" fill="none" stroke="#fff" stroke-width="2"><rect x="22" y="4" width="30" height="26"/><rect x="6" y="30" width="30" height="30"/><rect x="38" y="30" width="30" height="30"/><path d="M32 14h10M16 44h10M48 44h10"/><path d="M2 62h70M10 62v8M64 62v8"/></svg>
  </div>

  <div class="abs svclabel" style="left:133px">Local Moves</div>
  <div class="abs svclabel" style="left:372px">Interstate</div>
  <div class="abs svclabel" style="left:627px">Office Relocations</div>
  <div class="abs svclabel" style="left:886px">Packing Services</div>

  <div class="btn" style="left:502px;top:381px;width:196px;height:38px;background:#fff;color:var(--blue)">View more services</div>
</section>

<!-- testimonials -->
<div class="abs h2" style="left:418px;top:1956px"><span><b>Our</b> Testimonials</span><i></i></div>
<p class="abs" style="left:150px;top:2017px;width:900px;text-align:center;font-size:15.5px;line-height:34px">Lorem ipsum dolor sit amet, consectetur adipiscing elit, sed do eiusmod tempor incididunt ut labore et dolore magna aliqua enim ad minim veniam, quis nostrud</p>

<div class="abs tcard" style="left:111px">
  <p>Lorem ipsum dolor sit amet, consectetur adipiscing elit, sed do eiusmod tempor incididunt ut labore et dolore magna aliqua. Ut enim ad minim veniam, quis nostrud exercitation ullamco</p>
  <div class="avatar" role="img" aria-label="Portrait of the reviewer"></div>
  <div class="tname">Jordan Miles</div><div class="trole">General Manager</div>
</div>
<div class="abs tcard" style="left:445px">
  <p>Lorem ipsum dolor sit amet, consectetur adipiscing elit, sed do eiusmod tempor incididunt ut labore et dolore magna aliqua. Ut enim ad minim veniam, quis nostrud exercitation ullamco</p>
  <div class="avatar" role="img" aria-label="Portrait of the reviewer"></div>
  <div class="tname">Casey Ward</div><div class="trole">CEO</div>
</div>
<div class="abs tcard" style="left:778px">
  <p>Lorem ipsum dolor sit amet, consectetur adipiscing elit, sed do eiusmod tempor incididunt ut labore et dolore magna aliqua. Ut enim ad minim veniam, quis nostrud exercitation ullamco</p>
  <div class="avatar" role="img" aria-label="Portrait of the reviewer" style="background:linear-gradient(180deg,#7d8c86,#3f5a55)"></div>
  <div class="tname">Morgan Lee</div><div class="trole">General Manager</div>
</div>
<div class="btn" style="left:510px;top:2522px;width:180px;height:38px">View testimonials</div>

<!-- quote bar -->
<section class="abs quote">
  <div class="tab"></div>
  <h3>GET A QUOTE</h3>
  <div class="field" style="left:320px">NAME</div>
  <div class="field" style="left:491px">MOVE DATE</div>
  <div class="field" style="left:662px">LOCATIONS</div>
  <div class="field" style="left:834px">ITEMS</div>
  <div class="submit">SUBMIT NOW</div>
</section>

<!-- footer -->
<footer class="abs footer">
  <div class="fbrand"><i></i><span>Harbour Lane Removals</span></div>

  <div class="fh" style="left:403px">QUICK LINKS</div>
  <div class="fl" style="left:403px;top:96px">HOME<br>SERVICES<br>ABOUT US<br>TESTIMONIALS</div>

  <div class="fh" style="left:617px">SOCIAL LINKS</div>
  <div class="fl" style="left:617px;top:96px">UPDATES<br>COMMUNITY<br>GALLERY<br>VIDEOS</div>

  <div class="fh" style="left:846px">CONTACT US</div>
  <div class="ficon" style="left:846px;top:104px"><svg width="13" height="13" viewBox="0 0 24 24" fill="#fff"><path d="M6.6 10.8a15.1 15.1 0 0 0 6.6 6.6l2.2-2.2c.3-.3.7-.4 1-.2 1.1.4 2.3.6 3.6.6.6 0 1 .4 1 1V20c0 .6-.4 1-1 1A17 17 0 0 1 3 4c0-.6.4-1 1-1h3.5c.6 0 1 .4 1 1 0 1.3.2 2.5.6 3.6.1.3 0 .7-.2 1z"/></svg></div>
  <div class="fc" style="left:897px;top:114px">+1 555 010 2040</div>
  <div class="ficon" style="left:846px;top:160px"><svg width="13" height="10" viewBox="0 0 24 18"><path d="M1 1h22v16H1z" fill="#fff"/><path d="M1 1l11 9 11-9" stroke="#333" stroke-width="2" fill="none"/></svg></div>
  <div class="fc" style="left:897px;top:170px">HELLO@HARBOURLANEREMOVALS.EXAMPLE</div>

  <div class="frule"></div>
  <div class="copy">©2024 COPYRIGHTS - <b>HARBOUR LANE REMOVALS</b> - ALL RIGHTS RESERVED</div>
</footer>

</body>
</html>
```